Fire Risk Assessment App needs a sleek UI design

I need a sleek, modern but professional design for my 5 page Fire Risk Assessment App. Include gradient background, fire themed colours including reds, yellows, light orange and a touch of black. Design must ooze simplicity and professionalism. This is for the UK market. See attached images and word doc for more information.

Target Market(s)

General public and business owners

Industry/Entity Type

Technology / Fire Safety

Colors
00AB8E
00BBA5
67D7C9
C6EFE9
E9F9F6
59FF00
82FF00
B8FF75
E3FFCB
F4FFEA
FFC000
F8CF3A
FAE287
FDF2CF
FEFAEE
F0912C
F2A743
F7CA91
FBE8D2
FDF5EE
EE7325
F08F49
F5BC92
FAE3D3
FDF4ED
EB3D1F
EC4F4E
F09395
F8D3D4
FCEDEE

```html
<!DOCTYPE html>
<html lang="en">
<head>
<meta charset="UTF-8">
<title>Purchase – Fire Risk Assessment</title>
<link rel="stylesheet" href="https://fonts.googleapis.com/css2?family=Manrope:wght@400;500;600;700;800&display=swap">
<style>
  :root {
    --bg-top: #FEF8EA;
    --bg-bottom: #FBEED0;
    --ink: #1C1F2E;
    --ink-soft: #4A4D5A;
    --red: #EB3D1F;
    --orange-deep: #EE7325;
    --orange: #F0912C;
    --amber: #F2A743;
    --yellow: #FFC000;
    --white: #FFFFFF;
    --nav-bg: #FBEBC6;
    --nav-icon: #1F2A44;
  }
  * { box-sizing: border-box; margin: 0; padding: 0; }
  html, body { width: 1200px; height: 2598px; overflow: hidden; }
  body {
    font-family: "Manrope", sans-serif;
    background: linear-gradient(180deg, var(--bg-top) 0%, var(--bg-bottom) 100%);
    position: relative;
    color: var(--ink);
  }
  .page-title {
    position: absolute; top: 170px; left: 0; width: 100%;
    text-align: center; font-size: 70px; font-weight: 500; letter-spacing: -0.5px;
  }
  .page-subtitle {
    position: absolute; top: 278px; left: 0; width: 100%;
    text-align: center; font-size: 40px; font-weight: 400; color: var(--ink-soft);
  }
  .plan-card {
    position: absolute; left: 51px; top: 397px; width: 1098px; height: 1913px;
    border-radius: 64px; overflow: hidden;
    background:
      radial-gradient(ellipse 90% 45% at 50% 105%, rgba(255,192,0,0.95) 0%, rgba(255,192,0,0) 100%),
      linear-gradient(200deg, var(--red) 0%, var(--orange-deep) 30%, var(--orange) 60%, var(--yellow) 100%);
  }
  .plan-card__heading {
    position: absolute; top: 70px; left: 0; width: 100%;
    text-align: center; color: var(--white);
    font-size: 47px; font-weight: 600; line-height: 62px; letter-spacing: 0.5px;
  }
  .plan-option {
    position: absolute; left: 55px; width: 988px; height: 320px;
    border-radius: 32px; overflow: hidden;
    background: linear-gradient(180deg, rgba(255,255,255,0.55) 0%, rgba(255,255,255,0.22) 28%, rgba(255,255,255,0.18) 100%);
    border: 2px solid rgba(255,255,255,0.25);
    color: var(--white); text-align: center;
  }
  .plan-option--bronze { top: 265px; }
  .plan-option--silver { top: 617px; }
  .plan-option--gold { top: 969px; }
  .plan-option--platinum { top: 1321px; }
  .plan-option__radio {
    position: absolute; left: 42px; top: 42px; width: 78px; height: 78px;
    border-radius: 50%; border: 5px solid rgba(255,255,255,0.75);
  }
  .plan-option__name { position: absolute; top: 70px; width: 100%; font-size: 42px; font-weight: 600; letter-spacing: 0.5px; }
  .plan-option__count { position: absolute; top: 138px; width: 100%; font-size: 31px; font-weight: 400; opacity: 0.9; }
  .plan-option__was { position: absolute; top: 190px; width: 100%; font-size: 33px; font-weight: 400; text-decoration: line-through; opacity: 0.85; }
  .plan-option__price { position: absolute; top: 245px; width: 100%; font-size: 43px; font-weight: 700; }
  .plan-option--bronze .plan-option__price { top: 190px; }
  .checkout-button {
    position: absolute; left: 55px; top: 1699px; width: 988px; height: 147px;
    border-radius: 74px;
    background: linear-gradient(90deg, var(--red) 0%, #EC4F2E 60%, var(--orange-deep) 100%);
    box-shadow: 0 14px 30px rgba(180,50,10,0.35);
    color: var(--white); font-size: 45px; font-weight: 500;
    display: flex; align-items: center; justify-content: center;
  }
  .checkout-button__icon {
    position: absolute; left: 12px; top: 12px; width: 123px; height: 123px;
    border-radius: 50%; background: var(--amber);
    display: flex; align-items: center; justify-content: center;
  }
  .tab-bar {
    position: absolute; left: 0; top: 2381px; width: 1200px; height: 217px;
    background: var(--nav-bg);
  }
  .tab-bar__indicator {
    position: absolute; left: 384px; top: 0; width: 138px; height: 10px;
    border-radius: 0 0 6px 6px; background: var(--orange-deep);
  }
  .tab-bar__item { position: absolute; top: 70px; width: 80px; height: 80px; }
</style>
</head>
<body>
  <h1 class="page-title">Purchase</h1>
  <p class="page-subtitle">Lorem Ipsum is simply dummy text</p>

  <section class="plan-card">
    <h2 class="plan-card__heading">FIRE RISK ASSESSMENT<br>PAYMENT OPTIONS</h2>

    <div class="plan-option plan-option--bronze">
      <span class="plan-option__radio"></span>
      <div class="plan-option__name">BRONZE</div>
      <div class="plan-option__count">1 Fire Risk Assessment</div>
      <div class="plan-option__price">£19.99</div>
    </div>
    <div class="plan-option plan-option--silver">
      <span class="plan-option__radio"></span>
      <div class="plan-option__name">SILVER</div>
      <div class="plan-option__count">3 Fire Risk Assessments</div>
      <div class="plan-option__was">£59.97</div>
      <div class="plan-option__price">£54.99</div>
    </div>
    <div class="plan-option plan-option--gold">
      <span class="plan-option__radio"></span>
      <div class="plan-option__name">GOLD</div>
      <div class="plan-option__count">5 Fire Risk Assessments</div>
      <div class="plan-option__was">£99.95</div>
      <div class="plan-option__price">£89.99</div>
    </div>
    <div class="plan-option plan-option--platinum">
      <span class="plan-option__radio"></span>
      <div class="plan-option__name">PLATINUM</div>
      <div class="plan-option__count">10 Fire Risk Assessments</div>
      <div class="plan-option__was">£199.90</div>
      <div class="plan-option__price">£174.99</div>
    </div>

    <div class="checkout-button">
      <span class="checkout-button__icon">
        <svg width="52" height="48" viewBox="0 0 26 24" aria-hidden="true">
          <path d="M9 5V3.5A1.5 1.5 0 0 1 10.5 2h5A1.5 1.5 0 0 1 17 3.5V5" fill="none" stroke="#fff" stroke-width="2"/>
          <rect x="2" y="5" width="22" height="16" rx="3" fill="#fff"/>
        </svg>
      </span>
      Checkout
    </div>
  </section>

  <nav class="tab-bar">
    <span class="tab-bar__indicator"></span>
    <svg class="tab-bar__item" style="left:117px" viewBox="0 0 24 24" aria-label="Dashboard">
      <circle cx="12" cy="12" r="9.5" fill="none" stroke="var(--nav-icon)" stroke-width="2.6"/>
      <path d="M12 12 L16.5 7.5" stroke="var(--nav-icon)" stroke-width="2.6" stroke-linecap="round"/>
      <circle cx="12" cy="12" r="2" fill="var(--nav-icon)"/>
      <path d="M6.5 12a5.5 5.5 0 0 1 5.5-5.5" fill="none" stroke="var(--nav-icon)" stroke-width="2" stroke-linecap="round"/>
    </svg>
    <svg class="tab-bar__item" style="left:408px" viewBox="0 0 24 24" aria-label="Purchase">
      <rect x="2" y="4.5" width="20" height="15" rx="3" fill="var(--orange-deep)"/>
      <rect x="2" y="8.5" width="20" height="3" fill="#FBD3B0"/>
      <rect x="5" y="14.5" width="5" height="2" rx="1" fill="#FBD3B0"/>
    </svg>
    <svg class="tab-bar__item" style="left:706px" viewBox="0 0 24 24" aria-label="Messages">
      <path d="M4 3h16a2 2 0 0 1 2 2v11a2 2 0 0 1-2 2H10l-5 4v-4H4a2 2 0 0 1-2-2V5a2 2 0 0 1 2-2z" fill="var(--nav-icon)"/>
      <rect x="6" y="8" width="12" height="1.8" rx="0.9" fill="var(--nav-bg)"/>
      <rect x="6" y="11.5" width="8" height="1.8" rx="0.9" fill="var(--nav-bg)"/>
    </svg>
    <svg class="tab-bar__item" style="left:1003px" viewBox="0 0 24 24" aria-label="Account">
      <circle cx="9.5" cy="7" r="4.5" fill="var(--nav-icon)"/>
      <path d="M1.5 21.5c0-4.5 3.6-8 8-8 2 0 3.7.6 5 1.7V21.5z" fill="var(--nav-icon)"/>
      <path d="M15 18h7M19 15l3 3-3 3" fill="none" stroke="var(--nav-icon)" stroke-width="2.2" stroke-linecap="round" stroke-linejoin="round"/>
    </svg>
  </nav>
</body>
</html>
```